U.S. Popcorn company needs business cards

We are a popcorn company that manufactures popcorn and sells it to grocery stores worldwide. Our theme is "Americana" and our logo is U.S. route 66 which is the most famous highway in the U.S.

We would like the design to be simple and to use both sides. On the back side we would like to see just the logo and website. The front would be normal details

Target Market(s)

Wholesalers, grocers and distributors

Industry/Entity Type

Manufacture

Contact Information for Business Card

Business name: Prairie Lantern Popcorn
Phone: +1 555 308 4726
Email: Dale@prairielanternpopcorn.com
website: www.prairielanternpopcorn.com
Tag Line: "POPular for a reason"
Name: Dale Whitcombe
Title: Founder/President

Requirements
Must have
• Either this design should be fun or clean and simple. I will let you show me your thougths.
Nice to have
• Anything that ties in the real Hwy Route 66.
• Colors might need to be red, white and blue incorporated.
Should not have
• Not be too busy.

```html
<!DOCTYPE html>
<html lang="en">
<head>
<meta charset="utf-8">
<title>Prairie Lantern Popcorn – Business Cards</title>
<link rel="stylesheet" href="https://fonts.googleapis.com/css2?family=Open+Sans:wght@600;700&family=Questrial&display=swap">
<style>
  :root {
    --backdrop: #e4e4e4;
    --card: #ffffff;
    --navy: #1c3164;
    --red: #d42027;
    --ink: #2b3d6b;
    --muted: #3a4a72;
  }
  * { box-sizing: border-box; margin: 0; padding: 0; }
  html, body { width: 1200px; height: 576px; overflow: hidden; }
  body {
    background: var(--backdrop);
    position: relative;
    font-family: "Questrial", "Century Gothic", sans-serif;
  }
  .card {
    position: absolute;
    top: 138px;
    width: 482px;
    height: 294px;
    background: var(--card);
    border-radius: 8px;
    box-shadow: 0 2px 5px rgba(0,0,0,0.22);
    overflow: hidden;
  }
  .card--back { left: 82px; }
  .card--front { left: 602px; }

  .brand {
    position: absolute;
    display: flex;
    align-items: center;
    gap: 10px;
    transform: translate(-50%, -50%);
  }
  .brand__dot {
    width: 22px; height: 22px;
    border-radius: 50%;
    background: var(--red);
    flex: none;
  }
  .brand__name {
    font-family: "Open Sans", sans-serif;
    font-weight: 700;
    font-size: 23px;
    line-height: 1.1;
    color: var(--navy);
    text-transform: uppercase;
  }
  .card--back .brand { left: 242px; top: 134px; }
  .card--front .brand { left: 122px; top: 118px; }
  .card--front .brand__name { font-size: 20px; }

  .website-line {
    position: absolute;
    left: 0; right: 0;
    top: 256px;
    display: flex;
    align-items: center;
    justify-content: center;
    gap: 14px;
    font-family: "Open Sans", sans-serif;
    font-weight: 600;
    font-size: 11.5px;
    color: var(--navy);
  }
  .website-line__rule {
    width: 50px; height: 2px;
    background: var(--navy);
    border-radius: 1px;
  }

  .person {
    position: absolute;
    right: 18px;
    top: 30px;
    text-align: right;
  }
  .person__name {
    font-family: "Open Sans", sans-serif;
    font-weight: 600;
    font-size: 21px;
    color: var(--red);
    line-height: 1.1;
  }
  .person__title {
    font-size: 12px;
    color: var(--muted);
    margin-top: 2px;
  }
  .tagline {
    position: absolute;
    right: 18px;
    top: 92px;
    font-size: 15px;
    color: var(--ink);
  }
  .tagline strong {
    color: var(--red);
    font-family: "Open Sans", sans-serif;
    font-weight: 700;
  }

  .wave { position: absolute; left: 0; bottom: 0; width: 482px; height: 294px; }

  .contacts {
    position: absolute;
    right: 14px;
    top: 218px;
    list-style: none;
    text-align: right;
    color: #ffffff;
    font-size: 12.5px;
    line-height: 17.5px;
  }
  .contacts li { display: flex; align-items: center; justify-content: flex-end; gap: 6px; }
  .contacts svg { width: 10px; height: 10px; fill: var(--red); flex: none; }
</style>
</head>
<body>

  <section class="card card--back" aria-label="Card back">
    <div class="brand">
      <span class="brand__dot"></span>
      <span class="brand__name">Prairie Lantern<br>Popcorn</span>
    </div>
    <div class="website-line">
      <span class="website-line__rule"></span>
      <span>www.prairielanternpopcorn.com</span>
      <span class="website-line__rule"></span>
    </div>
  </section>

  <section class="card card--front" aria-label="Card front">
    <svg class="wave" viewBox="0 0 482 294" preserveAspectRatio="none" aria-hidden="true">
      <path d="M0,294 L0,256 C110,292 220,262 300,218 C360,184 420,160 482,154 L482,294 Z" fill="var(--navy)"/>
      <path d="M0,222 C90,250 200,256 290,208 C360,172 420,148 482,138 L482,146 C420,154 360,182 300,220 C205,272 95,268 0,242 Z" fill="var(--red)"/>
      <path d="M40,236 C130,252 210,244 280,214 C210,252 120,258 40,236 Z" fill="var(--red)"/>
    </svg>

    <div class="brand">
      <span class="brand__dot"></span>
      <span class="brand__name">Prairie Lantern<br>Popcorn</span>
    </div>

    <div class="person">
      <p class="person__name">Dale Whitcombe</p>
      <p class="person__title">Founder/President</p>
    </div>

    <p class="tagline">"<strong>POP</strong>ular for a reason"</p>

    <ul class="contacts">
      <li>+1 555 308 4726
        <svg viewBox="0 0 10 10" aria-hidden="true"><path d="M2,0.5 L3.6,0.5 L4.2,2.8 L3.1,3.6 C3.6,4.8 5.2,6.4 6.4,6.9 L7.2,5.8 L9.5,6.4 L9.5,8 C9.5,9 8.8,9.5 8,9.5 C4,9.3 0.7,6 0.5,2 C0.5,1.2 1,0.5 2,0.5 Z"/></svg>
      </li>
      <li>prairielanternpopcorn.com
        <svg viewBox="0 0 10 10" aria-hidden="true"><circle cx="5" cy="5" r="4.5"/><path d="M0.5,5 H9.5 M5,0.5 C3,3 3,7 5,9.5 M5,0.5 C7,3 7,7 5,9.5" stroke="#1c3164" stroke-width="0.8" fill="none"/></svg>
      </li>
      <li>Dale@prairielanternpopcorn.com
        <svg viewBox="0 0 10 10" aria-hidden="true"><rect x="0.5" y="2" width="9" height="6.5" rx="0.8"/><path d="M0.8,2.4 L5,5.8 L9.2,2.4" stroke="#1c3164" stroke-width="0.8" fill="none"/></svg>
      </li>
    </ul>
  </section>

</body>
</html>
```